Tovami Easy to modify Email Template

I need an email template created that can be easily modified for each new email sent. What I'm trying to accomplish is a look and feel that is consistent with each email I send out. In a perfect world, I'd like a template to use as a newsletter/informational with product/service pictures and an easy way to create the text to go with it. Then I'd also like a second email that is for letting my clients know there is a promotion or sale going on. Again, something that can he easily modified. I use mail chimp and MindBody as my platform for emailing. If possible, I'd like a pop-up box or dialog box that will ask the ready to opt-in with their name and email address.
I tried to have this done last year on ArtBazaar but we could never get it to work on Mail Chimp - the black box on the attachment would never display or capture email addresses.
What was created for me last year on ArtBazaar is great with matching colors and different sections. What would be great, if possible, is to create a template where I can add different photos in the same section, different verbiage in the same section, etc.
I hope I explained it well enough.
Updates

Target Market(s)

Target market is female - 30 to 65 years old

Industry/Entity Type

Health And Wellness

Font styles to use
Serif
Other font styles liked:
• lato

Requirements
Must have
• 1) must be able to be edited (and not by a designer/programmer)
2) must have an option to capture email addresses so people can opt-in to future email campaigns
3) must have a Zen feel to it. We are a medical spa - a very relaxed office space
4) not be too busy
Nice to have
• I hope this isn't asking too much, but the email needs to be able to run on MailChimp with no glitches. I would like the template(s) to be easily modified. Maybe keep the header and footer the same, back ground the same, and just sections that can be modified. Keep the colors to match my logo and the design from last year.

```html
<!DOCTYPE html>
<html lang="en">
<head>
<meta charset="utf-8">
<title>Tovami Medispa Newsletter</title>
<link href="https://fonts.googleapis.com/css2?family=IBM+Plex+Sans:wght@300;400;500&family=Allura&display=swap" rel="stylesheet">
<style>
  :root {
    --green: #4b8a2a;
    --ink: #2b2b2b;
    --body-text: #555555;
    --white: #ffffff;
    --field-border: #cfcfcf;
    --footer: #262626;
  }
  * { margin: 0; padding: 0; box-sizing: border-box; }
  html, body { width: 1200px; height: 4567px; overflow: hidden; background: var(--white); }
  body { font-family: "IBM Plex Sans", sans-serif; color: var(--body-text); position: relative; }

  .brand { position: absolute; display: flex; align-items: center; color: var(--ink); font-weight: 500; white-space: nowrap; z-index: 2; }
  .brand-dot { border-radius: 50%; background: var(--ink); flex: none; }
  .brand-header { left: 92px; top: 120px; height: 220px; gap: 30px; font-size: 58px; }
  .brand-header .brand-dot { width: 220px; height: 220px; }
  .brand-signup { left: 372px; top: 3738px; height: 148px; gap: 24px; font-size: 44px; }
  .brand-signup .brand-dot { width: 148px; height: 148px; }

  .header { position: absolute; left: 0; top: 0; width: 1200px; height: 554px; background: var(--white); }
  .header-photo { position: absolute; right: 0; top: 0; width: 390px; height: 480px;
    background: linear-gradient(160deg, #3f8a22 0%, #6aa23a 35%, #8d8b86 65%, #5b5a57 100%); }
  .deck-strip { position: absolute; left: 0; top: 480px; width: 1200px; height: 74px;
    background: linear-gradient(180deg, #d9d7d2, #b3b0a9); }

  .welcome { position: absolute; left: 0; top: 554px; width: 1200px; height: 1624px;
    background: linear-gradient(180deg, #f1efec 0%, #f7f6f4 50%, #fbfbfa 100%); }
  .welcome-kicker { position: absolute; left: 0; width: 1200px; top: 704px; text-align: center;
    font-size: 62px; font-weight: 400; color: var(--ink); letter-spacing: 1px; line-height: 72px; }
  .welcome-title { position: absolute; left: 0; width: 1200px; top: 790px; text-align: center;
    font-size: 96px; font-weight: 300; color: var(--green); line-height: 120px; white-space: nowrap; }
  .welcome-title .script { font-family: "Allura", cursive; color: var(--ink); font-size: 124px; }

  .copy { position: absolute; left: 0; width: 1200px; font-size: 28px; line-height: 50px; text-align: center; white-space: nowrap; z-index: 2; }
  .copy.on-green { color: var(--white); }

  .feature { position: absolute; left: 0; top: 2178px; width: 1200px; height: 1486px; background: var(--green); }
  .feature-photo { position: absolute; left: 82px; top: 1662px; width: 1044px; height: 832px;
    border: 14px solid var(--white); border-radius: 0 330px 0 240px;
    background: linear-gradient(135deg, #e6e7ea 0%, #f4f4f5 40%, #e9c7b0 65%, #d8d9dc 100%); }
  .feature-title { position: absolute; left: 0; width: 1200px; top: 2650px; text-align: center;
    color: var(--white); font-size: 92px; font-weight: 400; line-height: 150px; white-space: nowrap; }
  .feature-title .script { font-family: "Allura", cursive; font-size: 130px; margin-right: 24px; }

  .pill { position: absolute; left: 406px; width: 388px; height: 116px; border-radius: 0 70px 0 70px;
    display: flex; align-items: center; justify-content: center; font-size: 38px; font-weight: 500; letter-spacing: 1px; }
  .pill-light { background: var(--white); color: var(--green); top: 3390px; }
  .pill-dark { background: var(--green); color: var(--white); top: 4159px; }

  .signup { position: absolute; left: 0; top: 3664px; width: 1200px; height: 720px;
    background: linear-gradient(180deg, #f5f4f2, #f0eeeb); }
  .field { position: absolute; top: 3982px; width: 466px; height: 106px; background: var(--white);
    border: 2px solid var(--field-border); padding-left: 50px; display: flex; align-items: center; font-size: 27px; color: var(--ink); }
  .field-name { left: 120px; }
  .field-email { left: 613px; }

  .site-footer { position: absolute; left: 0; top: 4384px; width: 1200px; height: 183px; background: var(--footer);
    color: var(--white); font-size: 24px; line-height: 30px; text-align: center; padding-top: 96px; }
</style>
</head>
<body>
  <header class="header">
    <div class="header-photo" role="img" aria-label="Stacked spa stones with green leaves"></div>
    <div class="deck-strip" role="img" aria-label="Weathered wooden deck boards"></div>
  </header>
  <div class="brand brand-header"><span class="brand-dot"></span>Tovami Medispa</div>

  <section class="welcome" role="img" aria-label="Faint background of a relaxing hot stone massage"></section>
  <p class="welcome-kicker">WELCOME TO</p>
  <h1 class="welcome-title"><span class="script">Tovami</span>MEDISPA</h1>
  <p class="copy" style="top:978px">Lorem ipsum dolor sit amet, consectetur adipiscing elit, sed do eiusmod<br>tempor incididunt ut labore et dolore magna aliqis ipsum suspendisse<br>ultrices commodo viverra maecenas accumsan lacus vel facilisiorem<br>ipsum dolor sit amnsectetur adipiscinged do eiusmod tempcididunt<br>ut labore et dolore magna aliqis ipsum suspendisse</p>
  <p class="copy" style="top:1277px">Lorem ipsum dolor sit amet, consectetur adipiscing elit, sed do eiusmod<br>tempor incididunt ut labore et dolore magna aliqis ipsum suspendisse<br>ultrices commodo viverra maecenas accumsan lacus vel facilisiorem<br>ipsum dolor sit amnsectetur adipiscinged do eiusmod tempcididunt<br>ut labore et dolore magna aliqis ipsum suspendisse</p>

  <section class="feature" role="img" aria-label="Soft green background of spa stones and orchid"></section>
  <div class="feature-photo" role="img" aria-label="Client relaxing during a facial skin treatment"></div>
  <h2 class="feature-title"><span class="script">Page</span>TITLE HERE</h2>
  <p class="copy on-green" style="top:2864px">Lorem ipsum dolor sit amet, consectetur adipiscing elit, sed do eiusmod<br>tempor incididunt ut labore et dolore magna aliqis ipsum suspendisse<br>ultrices commodo viverra maecenas accumsan lacus vel facilisiorem<br>ipsum dolor sit amnsectetur adipiscinged do eiusmod tempcididunt<br>ut labore et dolore magna aliqis ipsum suspendisse</p>
  <p class="copy on-green" style="top:3163px">Sed do eiusmod tempor incididunt ut labore et dolore magna aliqis ipsum<br>suspendisse ultrices commodo viverra maecenas accumsan lacus vel<br>facilisiorem ipsum dolor sit amnsectetur adipiscinged</p>
  <a class="pill pill-light">READ MORE</a>

  <section class="signup" role="img" aria-label="Faint background of a spa massage"></section>
  <div class="brand brand-signup"><span class="brand-dot"></span>Tovami Medispa</div>
  <div class="field field-name">Enter Name</div>
  <div class="field field-email">Enter Email</div>
  <a class="pill pill-dark">SUBSCRIBE</a>

  <footer class="site-footer">© 2021 Tovami Medispa. All rights reserved.Privacy Terms of Use</footer>
</body>
</html>
```